Counseling Practice Business Card

I need a professional looking business card incorporating my new logo that was just completed. Card needs to incorporate my name and title, description of my specialty, my address, my phone number, my fax number, my email and my website URL. I need to be able to choose design on/with different paper colors and textures.
I do not have a lot of business card ideas so I am open to anything but I want bold,sharp, clear card without additional designs other than my logo (see attached file info). I am open to different color backgrounds or paper colors including black. I do not like traditional brackets around area codes in phone number or dashes between numbers in phone number. Am open to other ways of presenting including periods between numbers as appropriate. I do not know enough to know what I like yet but I want card to coordinate and work together with my logo. My practice emphasizes natural mental health interventions so any use of color (with background paper color or the blue and green in my logo) that elicits nature is nice. In addition to black, any natural brown or wood looking background might be desirable also. Most of the offerings so far look very similar and boring.

Target Market(s)

Potential therapy clients and other professionals

Contact Information for Business Card

Card information:
Gerald M. Whitcombe, Ph.D.
Licensed Clinical Psychologist
Integrative Health Coach
4812 Marlowe Ridge Blvd SE
Suite 310
Larkfield, GA 30417
(770) 415-2983 phone
(770) 581-4096 fax
drgeraldwhitcombe@quillmarsh.net
brightfernwellness.net

Font styles to use
Serif
Sans Serif
Other font styles liked:
• anything that you think looks crisp, clear and easily readable

Requirements
Must have
• Any color used should coordinate with my logo design (see attached files).
• Card should be printed horizontally so top and bottom are longest sides of rectangle.
• Background color or paper color should complement and highlight logo. Do not like a white background. black, grey, brown or any color my logo would blend well with.
Nice to have
• I would like designer to utilize color to highlight letters/name or phone-fax-web symbols.
• Bottom edge of card could be highlighted if appropriate to an idea.
Should not have
• I would NOT want the card to have a pure white background at all.
• No clear cards.
• Cards should be oriented with long sides on bottom and top, NOT sides. DO NOT LIKE THIS THIN TALL ORIENTATION.

```html
<!DOCTYPE html>
<html lang="en">
<head>
<meta charset="utf-8">
<title>Brightfern Wellness – Business Card</title>
<link href="https://fonts.googleapis.com/css2?family=Roboto:wght@400;500&family=Roboto+Condensed:wght@500;700&display=swap" rel="stylesheet">
<style>
  :root {
    --backdrop: #b8865a;
    --card: #121315;
    --brand-blue: #2f6fb6;
    --brand-green: #117a3d;
    --text-light: #d2d3d5;
    --text-url: #c4c5c8;
  }
  * { margin: 0; padding: 0; box-sizing: border-box; }
  html, body {
    width: 1200px; height: 960px; overflow: hidden;
    background: var(--backdrop);
    font-family: "Roboto", Arial, sans-serif;
  }
  .stage { position: relative; width: 1200px; height: 960px; }
  .card {
    position: absolute; width: 600px; height: 342px;
    background: var(--card);
    box-shadow: 0 3px 8px rgba(0,0,0,.35);
  }
  .card--front { left: 314px; top: 113px; }
  .card--back  { left: 311px; top: 472px; }

  .wordmark {
    display: flex; align-items: center; gap: 8px;
    color: var(--brand-blue); font-weight: 500; white-space: nowrap;
  }
  .wordmark__dot { border-radius: 50%; background: var(--brand-green); flex: none; }
  .card--front .wordmark { position: absolute; right: 36px; top: 74px; font-size: 27px; }
  .card--front .wordmark__dot { width: 14px; height: 14px; }
  .card--back .wordmark {
    position: absolute; left: 0; right: 0; top: 120px;
    justify-content: center; font-size: 44px; gap: 12px;
  }
  .card--back .wordmark__dot { width: 22px; height: 22px; }

  .identity { position: absolute; left: 30px; top: 143px; }
  .identity__name {
    font-family: "Roboto Condensed", Arial, sans-serif; font-weight: 700;
    font-size: 20px; line-height: 24px; color: var(--brand-blue);
    text-transform: uppercase; letter-spacing: .2px;
  }
  .identity__role { font-size: 15px; color: var(--brand-green); line-height: 19px; }

  .divider { position: absolute; left: 0; right: 0; top: 219px; height: 11px; display: flex; gap: 2px; }
  .divider__blue { width: 373px; background: var(--brand-blue); }
  .divider__green { flex: 1; background: var(--brand-green); }

  .contact { position: absolute; left: 31px; top: 250px; list-style: none; }
  .contact li {
    display: flex; align-items: center; gap: 9px;
    font-size: 14px; line-height: 18.5px; color: var(--text-light);
  }
  .contact svg { width: 13px; height: 13px; fill: var(--brand-blue); flex: none; }

  .address {
    position: absolute; right: 33px; top: 250px; text-align: right;
    font-size: 14px; line-height: 18.5px; color: var(--text-light); font-style: normal;
  }

  .back-url {
    position: absolute; left: 0; right: 0; top: 283px; text-align: center;
    font-size: 14px; letter-spacing: 4.2px; color: var(--text-url);
  }
</style>
</head>
<body>
<main class="stage">
  <section class="card card--front" aria-label="Card front">
    <div class="wordmark"><span class="wordmark__dot"></span>Brightfern Wellness</div>

    <div class="identity">
      <h1 class="identity__name">Gerald M. Whitcombe, Ph.D.</h1>
      <p class="identity__role">Licensed Clinical Psychologist</p>
      <p class="identity__role">Integrative Health Coach</p>
    </div>

    <div class="divider"><span class="divider__blue"></span><span class="divider__green"></span></div>

    <ul class="contact">
      <li>
        <svg viewBox="0 0 24 24" aria-hidden="true"><path d="M6.6 10.8a15.1 15.1 0 0 0 6.6 6.6l2.2-2.2a1 1 0 0 1 1-.25 11.4 11.4 0 0 0 3.6.57 1 1 0 0 1 1 1V20a1 1 0 0 1-1 1A17 17 0 0 1 3 4a1 1 0 0 1 1-1h3.5a1 1 0 0 1 1 1c0 1.25.2 2.45.57 3.57a1 1 0 0 1-.25 1z"/></svg>
        (770) 415-2983
      </li>
      <li>
        <svg viewBox="0 0 24 24" aria-hidden="true"><path d="M6 2h10l2 2v5H6z M3 10h18a1 1 0 0 1 1 1v7h-4v-3H6v3H2v-7a1 1 0 0 1 1-1z M7 16h10v6H7z"/></svg>
        (770) 581-4096
      </li>
      <li>
        <svg viewBox="0 0 24 24" aria-hidden="true"><path d="M2 5h20v2l-10 6L2 7z M2 9l10 6 10-6v10H2z"/></svg>
        drgeraldwhitcombe@quillmarsh.net
      </li>
    </ul>

    <address class="address">
      4812 Marlowe Ridge Blvd SE<br>
      Suite 310 Larkfield, GA 30417<br>
      www.brightfernwellness.net
    </address>
  </section>

  <section class="card card--back" aria-label="Card back">
    <div class="wordmark"><span class="wordmark__dot"></span>Brightfern Wellness</div>
    <p class="back-url">www.brightfernwellness.net</p>
  </section>
</main>
</body>
</html>
```